Brightmill Data Works

Our company is about IT hardwares and IT solutions. IT hardware such as PC, RAMS, storage and servers. IT solutions such as project management, BA. We are also selling new technology too.

Target Market(s)

Consumer, Small to Medium Business, Corporate

Requirements
Must have
• The business card must have the following:
• Name:
• Title:
• Contact Number:
• Email address:
• Website:
• Color: Must match the logo color upgrade

```html
<!DOCTYPE html>
<html lang="en">
<head>
<meta charset="utf-8">
<title>Brightmill Data Works – Business Card</title>
<link href="https://fonts.googleapis.com/css2?family=Saira:wght@400;600&display=swap" rel="stylesheet">
<style>
  :root {
    --backdrop-light: #e4e4e4;
    --backdrop-dark: #d3d3d3;
    --paper: #e3e3e3;
    --ink-dark: #3b3b3b;
    --band-black: #222222;
    --copper-light: #c08436;
    --copper-dark: #a25626;
    --copper-flat: #b77a35;
    --frame-grey: #6e6e6e;
    --deboss-grey: #6f6f6f;
    --white: #f4f4f4;
  }
  * { margin: 0; padding: 0; box-sizing: border-box; }
  html, body {
    width: 1200px; height: 878px; overflow: hidden;
  }
  body {
    position: relative;
    background: linear-gradient(160deg, var(--backdrop-light), var(--backdrop-dark));
    font-family: "Saira", sans-serif;
  }
  .card {
    position: absolute;
    top: 138px;
    width: 339px;
    height: 597px;
    overflow: hidden;
  }
  /* Front */
  .card-front { left: 230px; background: var(--paper); }
  .front-brand {
    position: absolute; top: 104px; left: 0; right: 0;
    text-align: center;
    color: var(--ink-dark);
    font-weight: 600;
    font-size: 34px;
    line-height: 38px;
    letter-spacing: 1px;
  }
  .name-band {
    position: absolute; top: 278px; left: 0; right: 0; height: 77px;
    background: var(--band-black);
    text-align: center;
  }
  .person-name {
    margin-top: 12px;
    color: var(--copper-light);
    font-size: 25px; line-height: 28px; font-weight: 400;
  }
  .person-title {
    color: var(--white);
    font-size: 20px; line-height: 22px; font-weight: 400;
  }
  .contact-panel {
    position: absolute; top: 355px; left: 0; right: 0; bottom: 0;
    background: linear-gradient(90deg, var(--copper-light), var(--copper-dark));
  }
  .contact-list {
    list-style: none;
    position: absolute; top: 73px; left: 0; right: 0;
    text-align: center;
    color: var(--white);
    font-size: 19px; line-height: 26px; letter-spacing: 0.6px;
  }
  /* Back */
  .card-back {
    left: 598px;
    background: var(--copper-flat);
    border: 5px solid var(--frame-grey);
  }
  .back-brand {
    position: absolute; top: 330px; left: 0; right: 0;
    text-align: center;
    color: var(--deboss-grey);
    font-weight: 600;
    font-size: 36px; line-height: 40px; letter-spacing: 1px;
  }
</style>
</head>
<body>
  <section class="card card-front">
    <div class="front-brand">BRIGHTMILL<br>DATA WORKS</div>
    <div class="name-band">
      <p class="person-name">DANIEL HARTLEY</p>
      <p class="person-title">MANAGER</p>
    </div>
    <div class="contact-panel">
      <ul class="contact-list">
        <li>+1-555-204-8817</li>
        <li>daniel@brightmilldata.com</li>
        <li>www.brightmilldata.com</li>
      </ul>
    </div>
  </section>

  <section class="card card-back">
    <div class="back-brand">BRIGHTMILL<br>DATA WORKS</div>
  </section>
</body>
</html>
```